Construction business card

I need a new business card, they can connect with my logo, brand.
What we do is residential house , design and build
I like: Navy blue / black
I attached our logo, brand,
and, some idea for business card.

```html
<!DOCTYPE html>
<html lang="en">
<head>
<meta charset="utf-8">
<title>Harlow Building Group – Business Card</title>
<link rel="stylesheet" href="https://fonts.googleapis.com/css2?family=Poppins:wght@400;500;700&display=swap">
<style>
  :root {
    --backdrop: #2b2c2e;
    --card: #1c1c1e;
    --brand-blue: #2f7fd6;
    --text-light: #f2f2f2;
    --emboss: #3a3a3d;
  }
  * { box-sizing: border-box; margin: 0; padding: 0; }
  html, body {
    width: 1200px; height: 939px; overflow: hidden;
    background: var(--backdrop);
    font-family: "Poppins", sans-serif;
  }
  .canvas { position: relative; width: 1200px; height: 939px; }
  .card {
    position: absolute;
    width: 580px; height: 331px;
    background: var(--card);
    box-shadow: 0 18px 40px rgba(0,0,0,.45);
    overflow: hidden;
  }
  .card--front { left: 70px; top: 80px; display: flex; align-items: center; justify-content: center; }
  .card--back { left: 550px; top: 530px; }

  .brand-mark {
    display: flex; align-items: center; gap: 14px;
    color: var(--text-light);
    font-weight: 700; font-size: 34px; letter-spacing: 1px;
    text-transform: uppercase; white-space: nowrap;
  }
  .brand-mark__square { width: 26px; height: 26px; background: var(--brand-blue); flex: none; }

  .brand-emboss {
    position: absolute; right: 34px; top: 34px;
    color: var(--emboss); font-weight: 700; font-size: 20px;
    text-transform: uppercase; letter-spacing: 1px; text-align: right; line-height: 1.15;
    white-space: nowrap;
  }

  .contact { position: absolute; left: 44px; top: 104px; color: var(--text-light); }
  .contact__name { color: var(--brand-blue); font-weight: 700; font-size: 25px; letter-spacing: .5px; text-transform: uppercase; line-height: 1.1; white-space: nowrap; }
  .contact__role { font-size: 15px; margin-top: 4px; }
  .contact__meta { font-size: 12.5px; line-height: 1.55; margin-top: 2px; }
  .contact__list { list-style: none; margin-top: 6px; font-size: 13px; }
  .contact__list li { display: flex; align-items: center; gap: 8px; line-height: 1.75; white-space: nowrap; }
  .contact__list svg { width: 14px; height: 14px; fill: var(--brand-blue); flex: none; }
</style>
</head>
<body>
<main class="canvas">
  <section class="card card--front" aria-label="Card front">
    <div class="brand-mark">
      <span class="brand-mark__square"></span>
      <span>Harlow Building Group</span>
    </div>
  </section>

  <section class="card card--back" aria-label="Card back">
    <div class="brand-emboss">Harlow<br>Building Group</div>
    <div class="contact">
      <h1 class="contact__name">Aaron Minh Cole</h1>
      <p class="contact__role">Director</p>
      <p class="contact__meta">HARLOW BUILDING GROUP PTY LTD<br>ABN: 48 302 551 776</p>
      <ul class="contact__list">
        <li><svg viewBox="0 0 16 16"><rect x="4" y="1" width="8" height="14" rx="1.5"/></svg>0400 555 318</li>
        <li><svg viewBox="0 0 16 16"><path d="M1 3h14v10H1z M1 3l7 6 7-6"/></svg>info@harlowbuildinggroup.com.au</li>
        <li><svg viewBox="0 0 16 16"><path d="M8 1a5 5 0 0 0-5 5c0 4 5 9 5 9s5-5 5-9a5 5 0 0 0-5-5zm0 7a2 2 0 1 1 0-4 2 2 0 0 1 0 4z"/></svg>27 Ashgrove St, Elmvale, VIC 3999</li>
        <li><svg viewBox="0 0 16 16"><circle cx="8" cy="8" r="7"/></svg>www.harlowbuildinggroup.com.au</li>
      </ul>
    </div>
  </section>
</main>
</body>
</html>
```